web Design for Architecture and Interior Design Firm

This is a complete redesign of an architecture and interior design firm.( http://www.qlbrankworks.com )
We have established a new look-n-feel for them and need to apply it to the new site/new architecture. Wireframes attached with logo and PDF of new brochure.
This will require a quck turn-around. The client is expecting a very modern design with web 2.0 in mind.
Again very quick turn-around! If you cannot commit to a Friday deliverable, do not bid! Must be completed by no later than Friday!

```html
<!DOCTYPE html>
<html lang="en">
<head>
<meta charset="utf-8">
<title>Quillan Brank — Portfolio</title>
<link href="https://fonts.googleapis.com/css2?family=Arimo:wght@400;700&family=Hind:wght@300;400&display=swap" rel="stylesheet">
<style>
:root{
  --black:#000;
  --band:#2e3130;
  --column:#262a2a;
  --card:#4b4c4b;
  --gold:#8d8550;
  --text:#f2f2f2;
  --muted:#b9b9b9;
  --salmon:#f3a79a;
  --red:#d0202e;
  --brand-grey:#6e6450;
  --active:#a8c6b0;
  --search:#b5b5b5;
}
*{margin:0;padding:0;box-sizing:border-box}
html,body{width:1200px;height:1200px;overflow:hidden;background:var(--black)}
body{font-family:"Arimo",Arial,sans-serif;color:var(--text);position:relative}
.abs{position:absolute}
.header{left:0;top:0;width:1200px;height:133px;background:var(--black)}
.brand{left:110px;top:34px;font-size:44px;letter-spacing:-1px;color:var(--brand-grey);font-family:"Hind",sans-serif;font-weight:400;line-height:1;white-space:nowrap}
.brand-rule{left:110px;top:86px;width:347px;height:1px;background:#444}
.tagline{left:190px;top:88px;font-family:"Hind",sans-serif;font-weight:300;font-size:22px;color:#777;white-space:nowrap}
.search{left:873px;top:80px;width:192px;height:20px;border-radius:5px;background:var(--search);font-size:9px;letter-spacing:1px;color:#222;padding:5px 10px}
.rule{left:0;width:1200px;height:2px;background:var(--gold)}
.band{left:0;top:135px;width:1200px;height:965px;background:var(--band)}
.column{left:100px;top:135px;width:368px;height:822px;background:var(--column)}
.hero{left:468px;top:135px;width:632px;height:965px;
  background:linear-gradient(90deg,#8a4a36 0%,#c8593c 30%,#e9e6dc 55%,#9fb5c4 80%,#d8dbd6 100%)}
.hero::after{content:"";position:absolute;left:0;right:0;bottom:0;height:260px;background:linear-gradient(180deg,rgba(0,0,0,0),rgba(70,70,70,.85))}
.veil{left:468px;top:135px;width:253px;height:965px;background:rgba(120,120,120,.35)}
.strip{left:0;top:959px;width:1200px;height:141px;background:rgba(55,58,57,.6)}
.heading{left:107px;top:160px;font-size:17px;font-weight:400}
.sub{left:107px;top:195px;font-size:14px;color:var(--muted);font-family:"Hind",sans-serif}
.card{left:105px;width:357px;height:110px;background:var(--card)}
.card .thumb{position:absolute;left:5px;top:9px;width:93px;height:93px}
.card h3{position:absolute;left:103px;top:9px;font-size:13px;font-weight:400;color:var(--text);white-space:nowrap}
.card ul{position:absolute;left:103px;top:31px;list-style:none}
.card li{font-size:12px;color:var(--salmon);height:19.5px;padding-left:15px;position:relative;white-space:nowrap}
.card li::before{content:"";position:absolute;left:0;top:3px;border-left:7px solid #eee;border-top:4px solid transparent;border-bottom:4px solid transparent}
.card .view{position:absolute;right:18px;bottom:7px;font-size:13px;color:var(--text)}
.t1{background:linear-gradient(135deg,#6a5b46,#a99a86 60%,#5a6f8c)}
.t2{background:linear-gradient(135deg,#a88a5a,#d8c9a8,#7a5a30)}
.t3{background:linear-gradient(180deg,#6f8fb0,#1e2c44 55%,#5a3022)}
.t4{background:linear-gradient(135deg,#b29772,#e2d2b5,#8a6a45)}
.t5{background:linear-gradient(135deg,#141823,#4a6a9a 50%,#c79a3a)}
.pager{left:224px;top:911px;display:flex;gap:3px;font-size:13px}
.pager span{width:16px;height:16px;background:#d8d8d8;color:#333;text-align:center;line-height:16px}
.pager .next{background:none;color:var(--text);width:auto;margin-left:3px}
.nav{left:552px;width:133px;text-align:center;font-size:14px;letter-spacing:.3px;color:#fff;border-bottom:1px solid rgba(255,255,255,.6);white-space:nowrap}
.nav.wide{left:521px;width:198px;border:none}
.nav.active{background:var(--active);color:#444;border:none;height:35px;line-height:35px}
.shot{top:975px;height:108px;border:1px solid var(--red)}
.s1{left:148px;width:73px;border:none;background:linear-gradient(90deg,#c8a06a,#8a3a22 40%,#3344aa)}
.s2{left:250px;width:151px;background:linear-gradient(135deg,#dcd8cc,#9c8a6a 60%,#5a4a30)}
.s3{left:418px;width:155px;background:linear-gradient(180deg,#b8c8d8,#1d2d48 50%,#3a2418)}
.s4{left:600px;width:145px;background:linear-gradient(135deg,#d8c29a,#8a6a40)}
.s5{left:764px;width:141px;background:linear-gradient(135deg,#6a7a6a,#d8d0c0 50%,#8a5a30)}
.s6{left:923px;width:145px;background:linear-gradient(90deg,#c8c0a8,#d2603e 45%,#c9c4b8)}
.arrow{top:1011px}
.copy{right:100px;top:1143px;font-size:10px;letter-spacing:.8px;color:#ddd;white-space:nowrap}
</style>
</head>
<body>
<div class="abs header"></div>
<div class="abs brand">QUILLAN BRANK</div>
<div class="abs brand-rule"></div>
<div class="abs tagline">people-focused design</div>
<div class="abs search">SEARCH</div>
<div class="abs rule" style="top:133px"></div>

<div class="abs band"></div>
<div class="abs column"></div>
<div class="abs hero" role="img" aria-label="Photo of a modern living room with orange walls, white sofa and tall windows"></div>
<div class="abs veil"></div>
<div class="abs strip"></div>
<div class="abs rule" style="top:957px"></div>
<div class="abs rule" style="top:1100px"></div>

<h1 class="abs heading">PORTFOLIO</h1>
<p class="abs sub">Project Pages</p>

<div class="abs card" style="top:227px">
  <div class="thumb t1" role="img" aria-label="Office reception photo"></div>
  <h3>Ashford Media Group, Tysons Corner, VA</h3>
  <ul><li>250 employees</li><li>88,000 SF</li><li>Fast-track completion</li></ul>
  <span class="view">Click To View</span>
</div>
<div class="abs card" style="top:348px">
  <div class="thumb t2" role="img" aria-label="Office interior photo"></div>
  <h3>The Capital Ledger</h3>
  <ul><li>Efficient use of existing space</li><li>Improve adjacencies of work groups</li><li>New workstation standards</li></ul>
  <span class="view">Click To View</span>
</div>
<div class="abs card" style="top:469px">
  <div class="thumb t3" role="img" aria-label="Conference room photo"></div>
  <h3>Veltron Systems, Rosslyn and Reston, VA</h3>
  <ul><li>Corporate Executive Offices</li><li>100,000 SF at 2200 Harlow Avenue</li><li>Fast-track completion</li></ul>
  <span class="view">Click To View</span>
</div>
<div class="abs card" style="top:592px">
  <div class="thumb t4" role="img" aria-label="Briefing lobby photo"></div>
  <h3>Veltron Systems, Chantilly, VA</h3>
  <ul><li>Desired recognizable position</li><li>Space for high-level briefing</li><li>Interactive plasma screen information</li></ul>
  <span class="view">Click To View</span>
</div>
<div class="abs card" style="top:713px">
  <div class="thumb t5" role="img" aria-label="Demonstration lab photo"></div>
  <h3>Harlan Pierce, Arlington, VA</h3>
  <ul><li>10,000 SF</li><li>Secure information area</li><li>Demonstration lab</li></ul>
  <span class="view">Click To View</span>
</div>

<div class="abs pager"><span>1</span><span>2</span><span>3</span><span>4</span><span>5</span><span>6</span><span class="next">Next</span></div>

<nav>
  <div class="abs nav" style="top:248px;height:21px">HOME</div>
  <div class="abs nav wide" style="top:292px">OUR COMPETITIVE EDGE</div>
  <div class="abs" style="left:552px;top:315px;width:133px;height:1px;background:rgba(255,255,255,.6)"></div>
  <div class="abs nav" style="top:342px;height:20px">SERVICES</div>
  <div class="abs nav active" style="top:375px">PORTFOLIO</div>
  <div class="abs nav" style="top:435px;height:18px">QBDS NEWS</div>
  <div class="abs nav" style="top:478px;height:22px">EMPLOYMENT</div>
  <div class="abs nav" style="top:522px;height:24px">CONTACT US</div>
</nav>

<svg class="abs arrow" style="left:108px" width="20" height="36" viewBox="0 0 20 36"><polygon points="18,0 18,36 0,18" fill="#fff"/></svg>
<div class="abs shot s1" role="img" aria-label="Hallway with blue chair photo"></div>
<div class="abs shot s2" role="img" aria-label="Open living space photo"></div>
<div class="abs shot s3" role="img" aria-label="Conference room photo"></div>
<div class="abs shot s4" role="img" aria-label="Curved staircase photo"></div>
<div class="abs shot s5" role="img" aria-label="Bedroom photo"></div>
<div class="abs shot s6" role="img" aria-label="Living room photo"></div>
<svg class="abs arrow" style="left:1079px" width="20" height="36" viewBox="0 0 20 36"><polygon points="2,0 2,36 18,18" fill="#fff"/></svg>

<p class="abs copy">Copyright 2005. Quillan Brank Design Studios.</p>
</body>
</html>
```